Stationery Design Project for Nimbora, Chicago

Nimbora, a street parking application which helps car drivers find a street parking spot by offering an ideal path along which to look for parking. This path is calculated by our algorithm based on data (e.g. historical data, baseball games schedule, etc.). Along this path the driver will find a spot and will also save 70% of the search time. Customer we target is reg. between 21 and 45 yo.

We envision something young, fresh, bright and original. Slightly abstract maybe. It should represent the idea and elements of finding street parking in the city, e.g. car(s), parking spot, people, city, etc. (just ideas!).

Logo is attached.

Requirement:
- Business Cards (2 Sided Full Color CMYK)
- Letterhead (1 Sided Full Color CMYK)
- Envelope (1 Sided Full Color CMYK)
- Sticker (1 Sided Full Color CMYK), round with a 2inch diameter.

Reason: We're starting to get more and more designs and need more time to look into all of them. Very exciting!! Thanks to everybody!

Hi all, we're in the process of selecting our favs. Though choices!!! Really good submissions. Will keep you posted and sorry for the delay.

Target Market(s)

Car drivers and owners between 21 and 45

Industry/Entity Type

Parking

Requirements
Must have
• Sticker should be round and include company URL nimbora.com and the new logo which we will attach soon.
Should not have
• Should not be too serious or boring.

```html
<!DOCTYPE html>
<html lang="en">
<head>
<meta charset="utf-8">
<title>Nimbora Business Card</title>
<link href="https://fonts.googleapis.com/css2?family=Open+Sans:wght@400;600;700&display=swap" rel="stylesheet">
<style>
  :root {
    --page-bg: #e4e6ea;
    --card-white: #ffffff;
    --ink-dark: #1b1b1f;
    --ink-grey: #4a4a4f;
    --navy: #1c2f93;
    --cyan: #12a3dd;
    --teal: #19b7ae;
    --band-glow: #14a9e6;
    --back-frame: #0a7dcc;
    --back-center: #2b8fe0;
    --back-edge: #1a3596;
    --mark-light: #3fa6f0;
    --mark-deep: #1538a8;
  }
  * { margin: 0; padding: 0; box-sizing: border-box; }
  html, body {
    width: 954px; height: 1200px; overflow: hidden;
    background: var(--page-bg);
    font-family: "Open Sans", Arial, sans-serif;
  }
  .canvas { position: relative; width: 954px; height: 1200px; }

  /* Front of card */
  .card-front {
    position: absolute; left: 76px; top: 96px;
    width: 795px; height: 456px;
    background: var(--card-white);
    border-radius: 28px; overflow: hidden;
    box-shadow: 0 6px 18px rgba(0,0,0,.25);
  }
  .brand-dot {
    position: absolute; left: 49px; top: 46px;
    width: 160px; height: 160px; border-radius: 50%;
    background: radial-gradient(circle at 40% 35%, var(--mark-light), var(--mark-deep) 75%);
  }
  .brand-name {
    position: absolute; left: 238px; top: 62px;
    font-size: 86px; font-weight: 600; line-height: 1;
    color: var(--ink-dark); letter-spacing: 1px;
  }
  .person {
    position: absolute; left: 84px; top: 303px;
    font-size: 23px; font-weight: 700; color: var(--navy);
  }
  .person .designation { font-size: 19px; color: var(--cyan); }
  .phones {
    position: absolute; left: 84px; top: 344px;
    font-size: 18px; color: var(--ink-grey);
  }
  .phones b { font-weight: 700; }
  .address {
    position: absolute; right: 41px; top: 317px;
    text-align: right; font-size: 18px; line-height: 27px; color: var(--ink-grey);
  }
  .accent-line {
    position: absolute; left: 0; top: 382px; width: 100%; height: 8px;
    background: var(--teal);
  }
  .contact-band {
    position: absolute; left: 0; top: 394px; width: 100%; height: 62px;
    background: radial-gradient(ellipse 40% 120% at 50% 100%, var(--band-glow), var(--navy) 80%);
    color: #fff; font-size: 18px;
    display: flex; align-items: center; justify-content: center;
    padding-bottom: 12px;
  }
  .contact-band b { font-weight: 700; }
  .contact-band .sep { margin: 0 10px; opacity: .7; }

  /* Back of card */
  .card-back {
    position: absolute; left: 73px; top: 648px;
    width: 795px; height: 454px;
    background: var(--back-frame);
    border-radius: 30px;
    box-shadow: 0 6px 18px rgba(0,0,0,.25);
  }
  .back-panel {
    position: absolute; left: 24px; top: 24px; right: 23px; bottom: 24px;
    background: radial-gradient(ellipse 60% 70% at 50% 40%, var(--back-center), var(--back-edge) 85%);
  }
  .back-dot {
    position: absolute; left: 282px; top: 40px;
    width: 236px; height: 236px; border-radius: 50%;
    background: radial-gradient(circle at 40% 35%, var(--mark-light), var(--mark-deep) 75%);
    box-shadow: 0 0 0 14px rgba(255,255,255,.08);
  }
  .back-name {
    position: absolute; left: 0; right: 0; top: 306px;
    text-align: center; font-size: 86px; font-weight: 600; line-height: 1;
    color: #fff; letter-spacing: 1px;
  }
</style>
</head>
<body>
<div class="canvas">
  <section class="card-front">
    <div class="brand-dot"></div>
    <div class="brand-name">nimbora</div>
    <div class="person">Your Name <span class="designation">- Designation</span></div>
    <div class="phones"><b>t</b> : 123-456-7890 &nbsp;|&nbsp; <b>c</b> : 123-456-7890</div>
    <div class="address">City Name, Street Name<br>State Name, Country Code</div>
    <div class="accent-line"></div>
    <div class="contact-band">
      <span><b>e</b> : name@website.com</span><span class="sep">|</span><span><b>w</b> : www.website.com</span>
    </div>
  </section>

  <section class="card-back">
    <div class="back-panel">
      <div class="back-dot"></div>
      <div class="back-name">nimbora</div>
    </div>
  </section>
</div>
</body>
</html>
```